Quiet Porch Podcast Cover Graphic

We need a graphic designed for a new podcast called "Quiet Porch." The graphic will be used on multiple podcasting platforms as the lead graphic advertising the podcast. The podcast consists of interviews of individuals sharing their life experiences including challenges, successes, lessons learned, and unexpected turns. The purpose of the podcast is to help listeners and participants learn from the life experiences of everyday neighbors. This podcast has a heavy Christian foundation on the parable of the good samaritan. We believe that through hearing the experiences of everyday neighbors, listeners can be strengthened, nourished, and aided to handle their own life challenges and trials. We would like the final design to be simple and reflective of the purpose and the parable of the good samaritan. The final design needs to have the title of the podcast, "Quiet Porch." We believe the best designs will limit the number of colors to less than 5 and will look good in a monochromatic version as well as a color version. We think the color white should be the main color. The graphic should be square in dimensions. We have considered having two hands grasping each other as if to lift the hand from below, but open to other creative simple takes to convey the lessons from the good samaritan.

```html
<!DOCTYPE html>
<html lang="en">
<head>
<meta charset="UTF-8">
<title>Quiet Porch Podcast Cover</title>
<link href="https://fonts.googleapis.com/css2?family=Oswald:wght@600&display=swap" rel="stylesheet">
<style>
  :root {
    --page-bg: #1c1c1f;
    --frame-green: #a8cf45;
    --sky-blue: #8ea8cc;
    --sky-haze: #d9d4cf;
    --horizon-gold: #f2c27e;
    --earth-dark: #140504;
    --title-white: #ffffff;
  }
  * { margin: 0; padding: 0; box-sizing: border-box; }
  html, body {
    width: 1200px;
    height: 1200px;
    overflow: hidden;
    background: var(--page-bg);
  }
  .cover {
    position: absolute;
    left: 100px;
    top: 100px;
    width: 1000px;
    height: 1000px;
    background: var(--frame-green);
    padding: 22px;
  }
  .cover-art {
    position: relative;
    width: 100%;
    height: 100%;
    overflow: hidden;
    background: var(--earth-dark);
  }
  .scene-photo {
    position: absolute;
    inset: 0;
    background:
      radial-gradient(ellipse 42% 38% at 50% 72%, rgba(120, 60, 20, 0.95) 0%, rgba(110, 55, 18, 0.6) 45%, rgba(20, 5, 4, 0) 100%),
      radial-gradient(ellipse 30% 14% at 50% 30%, rgba(255, 236, 190, 0.9) 0%, rgba(242, 194, 126, 0.6) 50%, rgba(242, 194, 126, 0) 100%),
      linear-gradient(to bottom,
        var(--sky-blue) 0%,
        var(--sky-haze) 16%,
        var(--horizon-gold) 30%,
        #8a4a1c 36%,
        #2a0d06 41%,
        var(--earth-dark) 60%,
        #1a0705 100%);
  }
  .title-block {
    position: absolute;
    left: 0;
    right: 0;
    bottom: 80px;
    display: flex;
    flex-direction: column;
    align-items: center;
  }
  .title-rule {
    width: 160px;
    height: 10px;
    background: var(--frame-green);
    margin-bottom: 36px;
  }
  .title {
    font-family: "Oswald", sans-serif;
    font-weight: 600;
    font-size: 190px;
    line-height: 1;
    letter-spacing: 8px;
    color: var(--title-white);
    text-transform: uppercase;
    text-align: center;
  }
  .title-line {
    display: block;
  }
</style>
</head>
<body>
  <main class="cover">
    <div class="cover-art">
      <div class="scene-photo" role="img" aria-label="Silhouettes of a group of people holding hands raised together on a hilltop against a sunset sky"></div>
      <div class="title-block">
        <div class="title-rule"></div>
        <h1 class="title">
          <span class="title-line">Quiet</span>
          <span class="title-line">Porch</span>
        </h1>
      </div>
    </div>
  </main>
</body>
</html>
```